Korvel CD Cover Design Project

I need a CD front cover(front inlay) , CD top artwork, CD back cover (back inlay)
i have provided a picture and other
Artiste Name: Korvel
Song Title: Tolulope (carry me Away)
Producer: Rinzo
Track-list
1. Tolulope (carry me Away)
2. Tolulope (carry me Away) acapella
3. Tolulope (carry me Away) (Instrumental)
stay connected:
twitter.com/markorvel
facebook.com/markorvel
www.korvelmusic.example
Management contact:
USA : Verity @ +12125550148 / verity@quillstonemedia.example
UK: Orla @ +447700900412/ +447700900786 / orlatunes@mailbox.example
Nigeria: Ngozi @ +2348000000193 / ngozi@korvelmusic.example
Target Market(s)
african Music consumers globally
Industry/Entity Type
Management
Look and feel
Each slider illustrates characteristics of the customer's brand and the style your logo design should communicate.

```html
<!DOCTYPE html>
<html lang="en">
<head>
<meta charset="utf-8">
<title>Korvel – Tolulope (carry me Away) – CD Top Artwork</title>
<link rel="stylesheet" href="https://fonts.googleapis.com/css2?family=Comfortaa:wght@700&display=swap">
<style>
  :root {
    --page-bg: #ffffff;
    --disc-black: #000000;
    --disc-shadow: #8c8c8c;
    --title-purple: #8a2a7e;
    --title-outline: #ffffff;
    --title-edge: #3a0d33;
    --hub-light: #f4f4f4;
    --hub-mid: #d6d6d6;
    --hub-edge: #b8b8b8;
    --photo-light: #d9d9d9;
    --photo-dark: #3b2f2a;
  }
  html, body {
    margin: 0;
    padding: 0;
    width: 1200px;
    height: 960px;
    overflow: hidden;
    background: var(--page-bg);
  }
  .cd-artwork {
    display: block;
    width: 1200px;
    height: 960px;
  }
  .disc-title {
    font-family: "Comfortaa", "Varela Round", sans-serif;
    font-weight: 700;
    fill: var(--title-purple);
    stroke: var(--title-outline);
    stroke-width: 7px;
    stroke-linejoin: round;
    paint-order: stroke fill;
  }
  .artist-name { font-size: 88px; letter-spacing: 2px; }
  .song-title { font-size: 46px; letter-spacing: 1px; }
</style>
</head>
<body>
<svg class="cd-artwork" viewBox="0 0 1200 960" xmlns="http://www.w3.org/2000/svg">
  <defs>
    <clipPath id="disc-face">
      <circle cx="600" cy="480" r="440"/>
    </clipPath>
    <radialGradient id="hub-ring" cx="50%" cy="50%" r="50%">
      <stop offset="40%" stop-color="var(--hub-light)"/>
      <stop offset="88%" stop-color="var(--hub-mid)"/>
      <stop offset="100%" stop-color="var(--hub-edge)"/>
    </radialGradient>
    <linearGradient id="artist-photo-tone" x1="0" y1="0" x2="0" y2="1">
      <stop offset="0%" stop-color="var(--photo-light)"/>
      <stop offset="45%" stop-color="var(--photo-dark)"/>
      <stop offset="100%" stop-color="var(--photo-light)"/>
    </linearGradient>
    <path id="artist-arc" d="M 682 254 A 240 240 0 0 1 808 600"/>
    <path id="title-outer-arc" d="M 366 615 A 270 270 0 0 1 445 259"/>
    <path id="title-inner-arc" d="M 486 677 A 228 228 0 0 1 580 253"/>
  </defs>

  <g class="disc">
    <circle class="disc-shadow" cx="606" cy="487" r="440" fill="var(--disc-shadow)"/>
    <circle class="disc-face" cx="600" cy="480" r="440" fill="var(--disc-black)"/>
  </g>

  <g class="disc-hub">
    <circle cx="600" cy="480" r="138" fill="url(#hub-ring)"/>
    <circle cx="600" cy="480" r="55" fill="#ffffff" stroke="var(--hub-edge)" stroke-width="1.5"/>
  </g>

  <g clip-path="url(#disc-face)">
    <path class="artist-photo" role="img" aria-label="Portrait photo of the artist Korvel in sunglasses and a grey t-shirt"
          d="M 600 650 Q 640 615 690 630 Q 730 650 735 720 L 760 800 Q 820 830 850 860 L 850 930 L 505 930 Q 520 870 590 830 L 590 760 Q 575 700 600 650 Z"
          fill="url(#artist-photo-tone)" stroke="#ffffff" stroke-width="5"/>
  </g>

  <text class="disc-title artist-name">
    <textPath href="#artist-arc" startOffset="50%" text-anchor="middle">Korvel</textPath>
  </text>
  <text class="disc-title song-title">
    <textPath href="#title-outer-arc" startOffset="50%" text-anchor="middle">Tolulope</textPath>
  </text>
  <text class="disc-title song-title">
    <textPath href="#title-inner-arc" startOffset="50%" text-anchor="middle">(carry me Away)</textPath>
  </text>
</svg>
</body>
</html>
```